Marwick Law Letterhead

We need a new letterhead design for a Law Firm. The address for the law firm is 1475 Calloway Street, Suite 210, Houston, Texas 77041. Phone Number: 832-361-9027; Fax Number: 832-614-7359. The logo is uploaded to the project.

```html
<!DOCTYPE html>
<html lang="en">
<head>
<meta charset="utf-8">
<title>Marwick Law Letterhead</title>
<link href="https://fonts.googleapis.com/css2?family=Montserrat:wght@400;500;600&display=swap" rel="stylesheet">
<style>
  :root {
    --red-bright: #e01b24;
    --red-deep: #6b0010;
    --navy: #14264f;
    --ink: #222226;
    --paper: #ffffff;
    --backdrop: #e9e9eb;
  }
  * { margin: 0; padding: 0; box-sizing: border-box; }
  html, body {
    width: 1200px; height: 960px; overflow: hidden;
    background: var(--backdrop);
    font-family: "Montserrat", Arial, sans-serif;
  }
  .letterhead {
    position: absolute; left: 275px; top: 20px;
    width: 650px; height: 920px;
    background: var(--paper);
    box-shadow: 0 6px 24px rgba(0,0,0,.12);
    overflow: hidden;
  }
  .header-wave, .footer-band { position: absolute; left: 0; width: 650px; }
  .header-wave { top: 0; height: 200px; }
  .footer-band { bottom: 0; height: 70px; }
  .brand {
    position: absolute; left: 70px; top: 210px;
    display: flex; align-items: center; gap: 10px;
  }
  .brand-mark { width: 20px; height: 20px; background: var(--red-bright); flex: none; }
  .brand-name {
    font-size: 22px; font-weight: 600; color: var(--navy);
    letter-spacing: .5px; line-height: 1;
  }
  .letter {
    position: absolute; left: 52px; top: 254px; width: 520px;
    color: var(--ink); font-size: 10px; line-height: 1.5;
  }
  .recipient { margin-bottom: 6px; }
  .recipient p { margin: 0; }
  .letter-body p { margin: 0 0 10px 28px; width: 470px; }
  .closing { margin: 4px 0 0 28px; font-size: 13px; }
  .signature {
    margin: 4px 0 0 28px; width: 110px; height: 28px;
    background: linear-gradient(90deg, #f1f1f3, #e4e4e8);
    border-radius: 3px;
  }
  .contact-lines {
    position: absolute; right: 52px; bottom: 80px;
    font-size: 11.5px; color: var(--ink);
  }
  .contact-lines li { list-style: none; display: flex; align-items: center; gap: 8px; margin-top: 4px; }
  .contact-lines svg { width: 12px; height: 12px; }
  .address {
    position: absolute; right: 40px; bottom: 16px;
    color: #fff; font-size: 11px; font-weight: 500; letter-spacing: .2px;
  }
</style>
</head>
<body>
<main class="letterhead">
  <svg class="header-wave" viewBox="0 0 650 200" aria-hidden="true">
    <defs>
      <linearGradient id="redFade" x1="0" y1="0" x2="1" y2="0">
        <stop offset="0" stop-color="#e01b24"/>
        <stop offset="1" stop-color="#6b0010"/>
      </linearGradient>
    </defs>
    <path d="M0 0 H615 C600 55 460 88 300 108 C150 126 60 140 22 190 L0 190 Z" fill="url(#redFade)"/>
    <path d="M636 18 C625 75 470 106 310 124 C170 140 70 152 36 200" fill="none" stroke="#14264f" stroke-width="6"/>
  </svg>

  <div class="brand">
    <span class="brand-mark"></span>
    <span class="brand-name">Marwick Law</span>
  </div>

  <section class="letter">
    <div class="recipient">
      <p>Mr/s</p>
      <p>First Name and Last Name</p>
      <p>Company Name</p>
      <p>Address</p>
    </div>
    <div class="letter-body">
      <p>Lorem ipsum dolor sit amet,consectetur adipiscing sed do eiusmod tempor incididunt laboreet dolore magna aliqua.Ut enim ad minim veniam, quis nostrud exercitation ullamco laboris nisi ut aliquip exea commodo consequat.Lorem ipsum dolor sit amet,consectetur adipiscing sed do eiusmod tempor incididunt labore et dolore magna aliqua. Ut enim</p>
      <p>Lorem ipsum dolor sit amet, consectetur adipiscing sed do eiusmod tempor incididunt labore et dolore magna aliqua. Ut enim ad minim veniam, quis nostrud exercitation ullamco laboris nisi ut aliquip exea commodo consequat.Duis aute irure dolor in reprehenderit in voluptate velit esse cillum irure dolor in reprehenderit in voluptate velit esse irure</p>
      <p>Lorem ipsum dolor sit amet, consectetur adipiscing sed do eiusmod tempor incididunt labore et dolore magna aliqua. consequat. Duis aute irure dolor in.reprehenderit in voluptate velit esse cillum dolore eu fugiat nulla pariatur. Excepteur sint occaecat cupidatat non proident, sunt in culpa qui officia deserunt mollit,</p>
      <p>Lorem ipsum dolor sit amet, consectetur adipiscing sed do eiusmod tempor incididunt labore et dolore magna aliqua. Ut enim Lorem ipsum dolor sit amet, consectetur adipiscing sed do eiusmod tempor incididunt labore et dolore magna aliqua. Ut enim Lorem ipsum aliqua.ipsum</p>
      <p>Lorem ipsum dolor sit amet, consectetur adipiscing sed do eiusmod tempor incididunt labore et dolore magna aliqua. Ut enim ad minim veniam, quis nostrud exercitation ullamco laboris nisi ut aliquip exea commodo consequat.Duis aute irure dolor in reprehenderit in voluptate velit esse cillum irure dolor in reprehenderit in voluptate velit esse irure</p>
      <p>Lorem ipsum dolor sit amet, consectetur adipiscing sed do eiusmod tempor incididunt labore et dolore magna aliqua. Ut enim ad minim veniam, quis nostrud exercitation ullamco laboris nisi ut aliquip exea commodo consequat.Duis aute irure dolor in reprehenderit in voluptate velit esse cillum irure dolor in reprehenderit in voluptate velit esse irure</p>
    </div>
    <p class="closing">Regards</p>
    <div class="signature" role="img" aria-label="Handwritten signature"></div>
  </section>

  <ul class="contact-lines">
    <li>
      <svg viewBox="0 0 24 24" aria-hidden="true"><path fill="#e01b24" d="M6.6 10.8a15 15 0 0 0 6.6 6.6l2.2-2.2a1 1 0 0 1 1-.25 11.4 11.4 0 0 0 3.6.57 1 1 0 0 1 1 1V20a1 1 0 0 1-1 1A17 17 0 0 1 3 4a1 1 0 0 1 1-1h3.5a1 1 0 0 1 1 1c0 1.25.2 2.45.57 3.57a1 1 0 0 1-.25 1z"/></svg>
      832-361-9027
    </li>
    <li>
      <svg viewBox="0 0 24 24" aria-hidden="true"><path fill="#e01b24" d="M6 3h12v5H6zM4 9h16a2 2 0 0 1 2 2v6h-4v4H6v-4H2v-6a2 2 0 0 1 2-2zm4 7v3h8v-3z"/></svg>
      832-614-7359
    </li>
  </ul>

  <svg class="footer-band" viewBox="0 0 650 70" aria-hidden="true">
    <rect x="0" y="8" width="650" height="5" fill="#14264f"/>
    <rect x="0" y="20" width="650" height="50" fill="url(#redFade)"/>
  </svg>
  <p class="address">1475 Calloway Street, Suite 210, Houston, Texas 77041</p>
</main>
</body>
</html>
```